Food Safety 1-California workers only

3.25" by 4.5" Black and White Magazine Ad
This ad is to train California workers only.
Workers will be trained on: Food Safety, FSMA (Food Safety Modernization Act), using equipment safety, food processing production skills, worker safety, supervisory skills, communication skills.
"FREE TRAINING", The company does the training or Harrowgate Instruction will provide the training.
Training grants range from $100,000 to $400,000.
Companies must be in business for profit.
Companies must train 200 employees or more.
This program is for California workers only.
Incumbent or new-hires are eligible.

Target Market(s)

California food processors, farms, food packaging, food processors, companies under FSMA, food safety, food production who need to train employees.

Industry/Entity Type

Food Production

Font styles to use
Serif
Sans Serif

Colors

Designer to choose colors to be used in the design.

Requirements
Must have
• This is a 3.25 inch by 4.5 inch magazine ad. It must be black and white. No color.
• The deliverable must be in basic PhotoShop. The ad does not need to include any graphics and be text only if needed. If you have a black and white graphic that will show well.
• Look at www.HGIPlateWatch..example
• Use the text from "TRAVO7-Photoshop-052018" file as your starting point.
Nice to have
• A black and white graphic about food. See www.HGIPlateWatch.example
Should not have
• No color.

```html
<!DOCTYPE html>
<html lang="en">
<head>
<meta charset="utf-8">
<title>Free Training – Harrowgate Instruction</title>
<link href="https://fonts.googleapis.com/css2?family=Oswald:wght@600;700&family=Libre+Baskerville:ital,wght@0,400;0,700;1,400;1,700&family=Open+Sans:wght@400;700&display=swap" rel="stylesheet">
<style>
  :root {
    --ink: #000000;
    --paper: #ffffff;
    --photo-light: #e0e0e0;
    --photo-mid: #9a9a9a;
    --photo-dark: #4a4a4a;
  }
  * { box-sizing: border-box; margin: 0; padding: 0; }
  html, body { width: 867px; height: 1200px; overflow: hidden; background: var(--paper); }
  .ad { position: relative; width: 867px; height: 1200px; background: var(--paper); overflow: hidden; }

  .ad__dark { position: absolute; left: 0; top: 0; width: 867px; height: 867px; background: var(--ink); }

  .headline {
    position: absolute; top: 0; left: 0; width: 100%;
    text-align: center; color: var(--paper);
    font-family: 'Oswald', sans-serif; font-weight: 700;
    font-size: 104px; letter-spacing: 2px; line-height: 1;
    transform: scaleY(1.55); transform-origin: top center;
  }
  .topics {
    position: absolute; top: 198px; left: 0; width: 100%;
    text-align: center; color: var(--paper);
    font-family: 'Libre Baskerville', serif; font-size: 27px;
  }

  .promise {
    position: absolute; top: 272px; left: 52px; right: 0; height: 150px;
    background: var(--paper); color: var(--ink);
    font-family: 'Libre Baskerville', serif; font-style: italic;
    padding-left: 28px;
  }
  .promise__line { display: block; font-size: 31px; line-height: 1; }
  .promise__line--one { margin-top: 22px; }
  .promise__line--two { margin-top: 14px; padding-left: 28px; }
  .promise__emph { font-weight: 700; font-size: 52px; letter-spacing: 1px; }

  .qualify {
    position: absolute; top: 464px; left: 112px;
    color: var(--paper); font-family: 'Open Sans', sans-serif;
  }
  .qualify__title { font-weight: 700; font-size: 30px; line-height: 44px; margin-bottom: 14px; }
  .qualify__list { list-style: none; }
  .qualify__item { font-size: 25px; line-height: 46px; }

  .food-art {
    position: absolute; left: 482px; top: 668px; width: 385px; height: 228px;
    background: radial-gradient(ellipse at 55% 55%, var(--photo-light) 0%, var(--photo-mid) 55%, var(--photo-dark) 100%);
    border-radius: 50% 40% 12px 12px / 60% 50% 12px 12px;
  }

  .contact { position: absolute; top: 915px; left: 0; width: 100%; text-align: center; color: var(--ink); font-family: 'Libre Baskerville', serif; }
  .contact__name { font-family: 'Oswald', sans-serif; font-weight: 600; font-size: 40px; letter-spacing: 1px; line-height: 56px; }
  .contact__company { font-family: 'Open Sans', sans-serif; font-weight: 700; font-size: 30px; line-height: 44px; }
  .contact__address { font-family: 'Open Sans', sans-serif; font-size: 19px; line-height: 26px; margin-top: 4px; }

  .links {
    position: absolute; top: 1086px; left: 95px; width: 720px;
    display: grid; grid-template-columns: 390px 330px; row-gap: 16px;
    font-family: 'Open Sans', sans-serif; font-size: 21px; line-height: 30px; color: var(--ink);
  }
  .links__item { display: flex; align-items: center; gap: 14px; }
  .links__icon { width: 28px; height: 28px; flex: none; }
</style>
</head>
<body>
<main class="ad">
  <div class="ad__dark"></div>

  <h1 class="headline">FREE TRAINING</h1>
  <p class="topics">Food Safety • FSMA • Production Skills • Worker Safety</p>

  <div class="promise">
    <span class="promise__line promise__line--one">WE DO THE <span class="promise__emph">TRAINING</span></span>
    <span class="promise__line promise__line--two">AND THE STATE <span class="promise__emph">PAYS</span> FOR IT!</span>
  </div>

  <section class="qualify">
    <h2 class="qualify__title">How to qualify:</h2>
    <ul class="qualify__list">
      <li class="qualify__item">Employees must attend at least 8 Hours of training</li>
      <li class="qualify__item">Incumbent or New-Hire workers are eligible</li>
      <li class="qualify__item">You must train 200 or more employees</li>
      <li class="qualify__item">Train California Workers Only</li>
      <li class="qualify__item">Trainees must earn $11/hour</li>
      <li class="qualify__item">Seasonal workers are eligible</li>
      <li class="qualify__item">Full-time workers only</li>
    </ul>
  </section>

  <div class="food-art" role="img" aria-label="Black and white photograph of a basket of fresh vegetables, fruit and bread"></div>

  <section class="contact">
    <p class="contact__name">MARCUS ELLERY</p>
    <p class="contact__company">Harrowgate Instruction Company, Inc.</p>
    <p class="contact__address">1800 Larkspur Avenue, Suite 310<br>Tustin, CA 92780</p>
  </section>

  <div class="links">
    <div class="links__item">
      <svg class="links__icon" viewBox="0 0 30 30" aria-hidden="true">
        <circle cx="15" cy="15" r="15" fill="#000"/>
        <circle cx="15" cy="15" r="8" fill="none" stroke="#fff" stroke-width="1.6"/>
        <ellipse cx="15" cy="15" rx="3.5" ry="8" fill="none" stroke="#fff" stroke-width="1.4"/>
        <line x1="7" y1="15" x2="23" y2="15" stroke="#fff" stroke-width="1.4"/>
      </svg>
      <span>www.HGICAL.example</span>
    </div>
    <div class="links__item">
      <svg class="links__icon" viewBox="0 0 30 30" aria-hidden="true">
        <rect x="3" y="7" width="24" height="16" fill="#000"/>
        <polyline points="3,7 15,17 27,7" fill="none" stroke="#fff" stroke-width="1.8"/>
      </svg>
      <span>M.Ellery@HGICAL.example</span>
    </div>
    <div class="links__item">
      <svg class="links__icon" viewBox="0 0 30 30" aria-hidden="true">
        <circle cx="15" cy="15" r="15" fill="#000"/>
        <circle cx="15" cy="15" r="8" fill="none" stroke="#fff" stroke-width="1.6"/>
        <ellipse cx="15" cy="15" rx="3.5" ry="8" fill="none" stroke="#fff" stroke-width="1.4"/>
        <line x1="7" y1="15" x2="23" y2="15" stroke="#fff" stroke-width="1.4"/>
      </svg>
      <span>www.HGIPlateWatch.example</span>
    </div>
    <div class="links__item">
      <svg class="links__icon" viewBox="0 0 30 30" aria-hidden="true">
        <path d="M8 4 L12 4 L14 10 L11 12 C12.5 15.5 14.5 17.5 18 19 L20 16 L26 18 L26 22 C26 24 24 26 22 26 C13 25 5 17 4 8 C4 6 6 4 8 4 Z" fill="#000"/>
      </svg>
      <span>(555) 014-2790</span>
    </div>
  </div>
</main>
</body>
</html>
```